Water ATM Card

Need a design for water ATM cards. Size of card is 3.375 x 2.125 inch
On the Front include the Cedar hollow Logo.
Bottom right corner should have Price $100
On the Back
This card is to be used to access water refills at any Cedar Hollow Water Vending Machines.
Please contact (869) 418 2930 or (869) 534 1276 or email clearflowbox@mailvista.example for any assistance or recharging of card.

```html
<!DOCTYPE html>
<html lang="en">
<head>
<meta charset="utf-8">
<title>Cedar Hollow Water Card</title>
<link href="https://fonts.googleapis.com/css2?family=Montserrat:wght@400;500;700&display=swap" rel="stylesheet">
<style>
  :root{
    --stage:#1c1c1c;
    --card-white:#ffffff;
    --brand-blue:#27509f;
    --brand-green:#2f9e47;
    --ink:#1b1b1b;
    --back-top:#2f7fc1;
    --back-bottom:#2e3b8c;
    --back-text:#f2f5ff;
  }
  *{margin:0;padding:0;box-sizing:border-box}
  html,body{width:1200px;height:1059px;overflow:hidden}
  body{background:var(--stage);font-family:"Montserrat",sans-serif;position:relative}
  .card{position:absolute;border-radius:26px;overflow:hidden}
  .card-front{left:256px;top:87px;width:689px;height:393px;background:var(--card-white)}
  .card-back{left:253px;top:546px;width:695px;height:395px;
    background:linear-gradient(170deg,var(--back-top) 0%,var(--back-bottom) 100%)}
  .holder-name{position:absolute;left:39px;top:66px;font-size:21px;font-weight:700;color:var(--brand-blue);letter-spacing:.3px}
  .holder-role{position:absolute;left:39px;top:96px;font-size:14px;font-weight:400;color:var(--ink);letter-spacing:.5px}
  .brand{position:absolute;right:40px;top:84px;display:flex;align-items:center;gap:10px}
  .brand-dot{width:18px;height:18px;border-radius:50%;background:var(--brand-green)}
  .brand-name{font-size:23px;font-weight:700;color:var(--brand-blue);letter-spacing:.3px}
  .contacts{position:absolute;left:38px;top:252px;list-style:none}
  .contacts li{display:flex;align-items:center;gap:8px;font-size:15px;color:var(--ink);height:24px}
  .contacts li:nth-child(1){margin-bottom:4px}
  .contacts svg{width:15px;height:15px;flex:none}
  .price{position:absolute;left:450px;top:312px;font-size:32px;font-weight:700;color:var(--brand-green)}
  .back-pattern{position:absolute;inset:0;
    background:linear-gradient(90deg,rgba(34,58,130,.35) 0%,rgba(60,100,180,.15) 60%,rgba(140,170,225,.2) 100%)}
  .back-brand{position:absolute;left:0;right:0;top:200px;display:flex;justify-content:center;align-items:center;gap:10px}
  .back-brand .brand-name{font-size:28px;color:var(--back-text)}
  .back-brand .brand-dot{width:20px;height:20px}
  .back-usage{position:absolute;left:50px;right:50px;top:262px;text-align:center;font-size:13px;line-height:20px;color:var(--back-text)}
  .back-note{position:absolute;left:0;right:0;top:344px;text-align:center;font-size:14.5px;color:var(--back-text)}
</style>
</head>
<body>
  <section class="card card-front">
    <h1 class="holder-name">DORIAN VALE</h1>
    <p class="holder-role">OWER</p>
    <div class="brand"><span class="brand-dot"></span><span class="brand-name">CEDAR HOLLOW</span></div>
    <ul class="contacts">
      <li><svg viewBox="0 0 24 24"><path fill="var(--brand-blue)" d="M6.6 10.8a15 15 0 0 0 6.6 6.6l2.2-2.2a1 1 0 0 1 1-.25 11 11 0 0 0 3.6.6 1 1 0 0 1 1 1V20a1 1 0 0 1-1 1A17 17 0 0 1 3 4a1 1 0 0 1 1-1h3.5a1 1 0 0 1 1 1c0 1.25.2 2.450.6 3.6a1 1 0 0 1-.25 1z"/></svg>(869) 418 2930</li>
      <li><svg viewBox="0 0 24 24"><rect x="6" y="1.5" width="12" height="21" rx="2" fill="var(--brand-blue)"/><rect x="8" y="4" width="8" height="14" fill="#fff"/></svg>(869) 534 1276</li>
      <li><svg viewBox="0 0 24 24"><rect x="2" y="5" width="20" height="14" rx="1.5" fill="var(--brand-blue)"/><path d="M3 6l9 7 9-7" stroke="#fff" stroke-width="1.6" fill="none"/></svg>clearflowbox@mailvista.example</li>
      <li><svg viewBox="0 0 24 24"><circle cx="12" cy="12" r="10" fill="var(--brand-blue)"/><path d="M2 12h20M12 2c3 3 3 17 0 20M12 2c-3 3-3 17 0 20" stroke="#fff" stroke-width="1.3" fill="none"/></svg>www.cedarhollowwater.example</li>
    </ul>
    <p class="price">Price $100</p>
  </section>

  <section class="card card-back">
    <div class="back-pattern" role="img" aria-label="Repeating faint brand pattern across the card back"></div>
    <div class="back-brand"><span class="brand-dot"></span><span class="brand-name">CEDAR HOLLOW</span></div>
    <p class="back-usage">This card is to be used to access water refills at any Cedar Hollow Water Vending Machines.<br>Please contact (869) 418 2930 or (869) 534 1276<br>or email clearflowbox@mailvista.example</p>
    <p class="back-note">for any assistance or recharging of card.</p>
  </section>
</body>
</html>
```